Voltaryn - Web Design Project

I am looking for a 5 page design.
I would like it to be like the design of this site: www.quorvexlabs.com.
Which means it can be all one page effectively. With quick scroll tabs at the top.
I would like it to include parallax scrolling (The parallax effect uses multiple backgrounds which seem to move at different speeds to create a sensation of depth (creating a faux-3D effect)).
I have uploaded my logo. I would like this to be used in the site design.
I would like the site design to include 3D DNA creative.
Please note the Pixmora photos attached do not belong to me they are purely to inspire creative ideas. However I would be more than happy to purchase these photos to use if the designer thought this would be beneficial.
Requirements
Must have
- parallax scrolling
DNA pictures (3D effect)
Please use site for reference: www.quorvexlabs.com
Use at least 1 of the logos in design...

```html
<!DOCTYPE html>
<html lang="en">
<head>
<meta charset="utf-8">
<title>Voltaryn – Hybrid Advertising</title>
<link rel="stylesheet" href="https://fonts.googleapis.com/css2?family=Fira+Sans+Condensed:wght@300;400&family=Roboto+Condensed:wght@300;400&family=Source+Sans+3:wght@400&display=swap">
<style>
  :root {
    --hero-deep: #22306a;
    --hero-mid: #4a5d95;
    --hero-light: #95a3c8;
    --helix-dark: #263468;
    --helix-light: #b9c3dd;
    --panel: rgba(236, 238, 245, 0.93);
    --nav-text: #5f6472;
    --logo-ink: #2d3a66;
    --about-deep: #03171c;
    --about-mid: #0b4650;
    --about-glow: #2fc4d8;
    --footer: #4b5a86;
    --white: #ffffff;
    --search-bg: #e4e6ec;
    --search-text: #c57a7a;
  }
  * { margin: 0; padding: 0; box-sizing: border-box; }
  html, body { width: 1039px; height: 1200px; overflow: hidden; }
  body {
    position: relative;
    font-family: "Fira Sans Condensed", "Roboto Condensed", sans-serif;
    color: var(--white);
    background: var(--footer);
  }
  .line { display: block; white-space: nowrap; }

  /* Hero */
  .hero {
    position: absolute; left: 0; top: 0; width: 1039px; height: 564px; overflow: hidden;
    background:
      radial-gradient(ellipse 420px 380px at 800px 260px, #5f71a8, transparent 70%),
      linear-gradient(135deg, var(--hero-light) 0%, var(--hero-mid) 45%, var(--hero-deep) 100%);
  }
  .hero-helix {
    position: absolute; left: 190px; top: 120px; width: 440px; height: 444px;
    background:
      radial-gradient(ellipse 50% 55% at 50% 55%, var(--helix-dark) 0%, rgba(50, 64, 120, 0.85) 45%, rgba(90, 106, 160, 0.35) 75%, transparent 100%);
  }
  .hero-helix-far {
    position: absolute; left: 0; top: 0; width: 250px; height: 564px;
    background: radial-gradient(ellipse 60% 60% at 40% 40%, rgba(200, 210, 232, 0.55), transparent 80%);
  }
  .hero-helix-right {
    position: absolute; left: 560px; top: 40px; width: 380px; height: 524px;
    background: radial-gradient(ellipse 50% 55% at 60% 55%, rgba(185, 196, 226, 0.35), transparent 80%);
  }
  .site-header {
    position: absolute; left: 154px; top: 0; width: 730px; height: 136px;
    background: var(--panel);
    border-radius: 0 0 12px 12px;
  }
  .brand {
    position: absolute; left: 22px; top: 18px; width: 130px; text-align: center;
    color: var(--logo-ink);
  }
  .brand-dot {
    display: block; width: 44px; height: 44px; margin: 0 auto 14px;
    border-radius: 50%; background: var(--logo-ink);
  }
  .brand-name {
    display: block; font-family: "Roboto Condensed", sans-serif; font-weight: 400;
    font-size: 18px; letter-spacing: 4.5px; line-height: 1;
  }
  .brand-tag {
    display: block; font-family: "Roboto Condensed", sans-serif; font-weight: 400;
    font-size: 7px; letter-spacing: 3.6px; margin-top: 2px;
  }
  .search {
    position: absolute; left: 544px; top: 48px; width: 166px; height: 28px;
    background: var(--search-bg);
    border: 1px solid #a9adb8; border-left-width: 2px; border-top-width: 2px;
    font-family: "Source Sans 3", sans-serif; font-size: 10px; font-style: italic;
    color: var(--search-text); padding: 7px 10px;
  }
  .search svg { position: absolute; right: 12px; top: 6px; }
  .main-nav {
    position: absolute; top: 106px; left: 0; width: 730px;
    font-family: "Roboto Condensed", sans-serif; font-weight: 300; font-size: 12px;
    letter-spacing: -0.2px; color: var(--nav-text);
  }
  .main-nav a { position: absolute; color: inherit; text-decoration: none; white-space: nowrap; }

  .slide-copy { position: absolute; left: 591px; top: 254px; width: 240px; }
  .slide-title { font-weight: 300; font-size: 40px; line-height: 1; }
  .slide-sub { font-weight: 300; font-size: 25px; line-height: 1.1; margin-top: 2px; }
  .slide-text { font-size: 9.6px; line-height: 12.8px; margin-top: 12px; }
  .slide-arrow {
    position: absolute; top: 313px; width: 35px; height: 35px; border-radius: 50%;
    background: rgba(220, 224, 236, 0.85);
  }
  .slide-arrow svg { position: absolute; left: 11px; top: 10px; }
  .slide-arrow.prev { left: 154px; }
  .slide-arrow.next { left: 850px; }

  /* About */
  .about {
    position: absolute; left: 0; top: 564px; width: 1039px; height: 550px; overflow: hidden;
    background:
      radial-gradient(ellipse 420px 260px at 160px 220px, rgba(30, 110, 125, 0.6), transparent 70%),
      linear-gradient(120deg, var(--about-mid) 0%, var(--about-deep) 55%, #062a31 100%);
  }
  .about-helix {
    position: absolute; left: 300px; top: 170px; width: 739px; height: 380px;
    background:
      radial-gradient(ellipse 38% 70% at 82% 45%, rgba(47, 196, 216, 0.55), transparent 75%),
      radial-gradient(ellipse 55% 30% at 55% 85%, rgba(47, 196, 216, 0.5), transparent 75%),
      radial-gradient(ellipse 45% 55% at 80% 70%, rgba(150, 225, 232, 0.25), transparent 80%);
  }
  .about-title {
    position: absolute; left: 153px; top: 76px;
    font-weight: 300; font-size: 40px; line-height: 1;
  }
  .about-text { font-size: 9.6px; line-height: 12.8px; }
  .about-intro { position: absolute; left: 154px; top: 129px; }
  .about-photo {
    position: absolute; left: 154px; top: 176px; width: 232px; height: 149px;
    background: linear-gradient(135deg, #e6ecf2 0%, #b9c8d6 50%, #7fa2b8 100%);
  }
  .about-col { position: absolute; left: 404px; top: 176px; }
  .about-col p + p { margin-top: 12.8px; }
  .about-outro { position: absolute; left: 152px; top: 340px; }

  /* Footer */
  .site-footer {
    position: absolute; left: 0; top: 1114px; width: 1039px; height: 86px;
    background: var(--footer);
    font-family: "Source Sans 3", sans-serif; font-size: 10px;
  }
  .footer-links { position: absolute; left: 154px; top: 26px; }
  .footer-links a { color: var(--white); text-decoration: none; }
  .footer-links .sep { margin: 0 4px; }
  .copyright { position: absolute; left: 154px; top: 42px; }
  .follow {
    position: absolute; left: 686px; top: 33px;
    font-family: "Roboto Condensed", sans-serif; font-size: 13px;
    letter-spacing: -0.4px; white-space: nowrap;
  }
  .social { position: absolute; left: 771px; top: 27px; display: flex; gap: 4px; }
  .social span {
    width: 26px; height: 26px; border-radius: 50%; background: var(--white);
  }
</style>
</head>
<body>

<section class="hero">
  <div class="hero-helix-far" role="img" aria-label="Faded DNA double helix in the background"></div>
  <div class="hero-helix-right" role="img" aria-label="Soft-focus DNA helix behind the slide text"></div>
  <div class="hero-helix" role="img" aria-label="Large 3D DNA double helix in the foreground"></div>

  <header class="site-header">
    <div class="brand">
      <span class="brand-dot"></span>
      <span class="brand-name">VOLTARYN</span>
      <span class="brand-tag">hybrid advertising</span>
    </div>
    <div class="search">Search
      <svg width="14" height="10" viewBox="0 0 14 10" aria-hidden="true">
        <circle cx="4" cy="4" r="3" fill="none" stroke="#c57a7a" stroke-width="1.4"/>
        <line x1="6.5" y1="5.5" x2="12" y2="9" stroke="#c57a7a" stroke-width="1.6"/>
      </svg>
    </div>
    <nav class="main-nav">
      <a href="#" style="left:294px">Home</a>
      <a href="#" style="left:347px">About Us</a>
      <a href="#" style="left:413px">Services</a>
      <a href="#" style="left:477px">Products</a>
      <a href="#" style="left:543px">Research</a>
      <a href="#" style="left:610px">Events</a>
      <a href="#" style="left:666px">Contact Us</a>
    </nav>
  </header>

  <a class="slide-arrow prev" href="#" aria-label="Previous slide">
    <svg width="12" height="15" viewBox="0 0 12 15"><path d="M8 1 L3 7.5 L8 14" fill="none" stroke="#fff" stroke-width="2.6"/></svg>
  </a>
  <a class="slide-arrow next" href="#" aria-label="Next slide">
    <svg width="12" height="15" viewBox="0 0 12 15"><path d="M4 1 L9 7.5 L4 14" fill="none" stroke="#fff" stroke-width="2.6"/></svg>
  </a>

  <div class="slide-copy">
    <h1 class="slide-title">Voltaryn</h1>
    <p class="slide-sub">Hybrid Advertising</p>
    <p class="slide-text">
      <span class="line">Lorem ipsum dolor sit amet, consectetuer adipiscing</span>
      <span class="line">elit. Aenean commodo ligula eget dolor. Aenean massa.</span>
      <span class="line">Cum sociis natoque penatibus et magnis dis parturient</span>
      <span class="line">montes, nascetur ridiculus mus. Donec quam felis,</span>
      <span class="line">ultricies nec, pellentesque eu, pretium quis, sem.</span>
    </p>
  </div>
</section>

<section class="about" aria-label="About Us">
  <div class="about-helix" role="img" aria-label="Glowing turquoise 3D DNA helix curving across the lower right"></div>
  <h2 class="about-title">About Us</h2>
  <p class="about-text about-intro">
    <span class="line">Lorem ipsum dolor sit amet, consectetuer adipiscing elit. Aenean commodo ligula eget dolor. Aenean massa. Cum sociis natoque penati-</span>
    <span class="line">bus et.Lorem ipsum dolor sit amet, consectetuer adipiscing elit. Aenean commodo ligula eget dolor. Aenean massa. Cum sociis natoque</span>
    <span class="line">penatibus etLorem ipsum dolor sit amet, consectetuer adipiscing elit.</span>
  </p>
  <div class="about-photo" role="img" aria-label="Photo of two scientists working with test tubes in a laboratory"></div>
  <div class="about-text about-col">
    <p>
      <span class="line">Lorem ipsum dolor sit amet, consectetuer adipiscing elit. Aenean commodo</span>
      <span class="line">ligula eget dolor. Aenean massa. Cum sociis natoque penatibus et magnis</span>
      <span class="line">dis parturient montes, nascetur ridiculus mus. Donec quam felis, ultricies</span>
      <span class="line">nec, pellentesque eu, pretium quis, sem.</span>
    </p>
    <p>
      <span class="line">Lorem ipsum dolor sit amet, consectetuer adipiscing elit. Aenean commodo</span>
      <span class="line">ligula eget dolor. Aenean massa. Cum sociis natoque penatibus et magnis</span>
      <span class="line">dis parturient montes, nascetur ridiculus mus. Donec quam felis, ultricies</span>
      <span class="line">nec, pellentesque eu, pretium quis, semLorem ipsum dolor sit amet, con-</span>
      <span class="line">sectetuer adipiscing elit. Aenean commodo ligula eget dolorLorem ipsum</span>
      <span class="line">dolor sit amet, consectetuer adipiscing elit. Aenean commodo ligula eget</span>
      <span class="line">dolor. Aenean massa. Cum sociis natoque penatibus etonsectetuer adipi-</span>
    </p>
  </div>
  <p class="about-text about-outro">
    <span class="line">Lorem ipsum dolor sit amet, consectetuer adipiscing elit. Aenean commodo ligula eget dolor. Aenean massa. Cum sociis natoque penati-</span>
    <span class="line">bus et magnis dis parturient montes, nascetur ridiculus mus. Donec quam felis, ultricies nec, pellentesque eu, pretium quis, sem.</span>
  </p>
</section>

<footer class="site-footer">
  <div class="footer-links">
    <a href="#">Login</a><span class="sep">|</span><a href="#">FAQ</a><span class="sep">|</span><a href="#">Contact Us</a><span class="sep">|</span><a href="#">Privacy</a><span class="sep">|</span><a href="#">Terms</a><span class="sep">|</span><a href="#">Sign up</a>
  </div>
  <p class="copyright">© Copyright 2013. All Rights Reserved</p>
  <p class="follow">FOLLOW US ON</p>
  <div class="social" aria-label="Social links">
    <span></span><span></span><span></span><span></span>
  </div>
</footer>

</body>
</html>
```